Redesign Canvas Art E-Commerce Website

Help! I hired a couple of companies on Brisklo.com to build and design an e-commerce website for me. After three long and painful months, I have one that I believe is functional on the back-end, but aesthetically on the front end is a mess.

We are a small family business that will take your digital photo and manipulate it into a digitally created oil, watercolor or impressionist style pieces of artwork that we print on museum quality, gallery grade canvas and ship to the customer, ready to hang.

We are looking to create an e-commerce website where a customer can choose their art style, upload a photo, choose their canvas size and orientation (horizontal or vertical) and checkout. Within 48 hours, we will send them back a proof of their newly created, customized artwork for them to approve or not approve. If they approve, we print, package and ship them the product. If they do not approve, we offer unlimited revisions until they are happy.

As I mentioned, the back end functionality is already there, just need design help. No coding required

Here is a link to the development page that they created: https://plumwickstudio.com/development/

As you can see, it looks off...doesnt line up properly, wasted space, weird font. Feel free to either correct the homepage they created or design an entirely new page. I am attaching some examples of before and after photos of artwork for reference. I also think the testimonials page and shop page can use a little style. The content is there and accurate, it just doesn't look pretty. Please keep in mind that our customers will probably not be very tech savvy. The customers will probably be sending us pics of kids, grandkids, pets, family portraits, vacation photos, etc.

Here is one of our competitors - www.gildavantry.com
Their website looks clean and inviting.

Thank you in advance! Im looking forward to seeing the results. I am including our logo in the attachments (I do not have it in a vector file, just a jpeg)

Target Market(s)

Non tech-savvy indiduals, 30-70 years old

Industry/Entity Type

Please look at https://plumwickstudio.com/development/ to see various pages and what the other designers did

Number of Pages Required

1 page

Requirements
Must have
• Verbiage on pages leave "as is" but feel free to change styles. Would like to keep existing four categories on homepage
Nice to have
• Warm and inviting homepage that evokes emotion

```html
<!DOCTYPE html>
<html lang="en">
<head>
<meta charset="utf-8">
<title>Brushtide Studio – One of a Kind Wall Art</title>
<link href="https://fonts.googleapis.com/css2?family=Montserrat:wght@400;500;600;700;800;900&family=Dancing+Script:wght@500;700&display=swap" rel="stylesheet">
<style>
:root{
  --blue:#1d6aae;
  --teal:#2aa3d3;
  --red:#e0401b;
  --ink:#333;
  --grey-band:#f1f1f0;
  --sky-band:#e6f4fa;
  --dark:#1d2a2a;
  --white:#fff;
}
*{box-sizing:border-box;margin:0;padding:0}
html,body{width:1200px;height:5376px;overflow:hidden}
body{position:relative;background:var(--white);font-family:'Montserrat',sans-serif;color:var(--ink)}
.abs{position:absolute}
.heading{font-family:'Montserrat',sans-serif;font-weight:900;color:var(--blue);letter-spacing:.5px}
.center{left:0;width:1200px;text-align:center}
.script{font-family:'Dancing Script',cursive;color:var(--teal);font-weight:500}
.btn{position:absolute;background:var(--red);color:var(--white);font-weight:700;font-size:14px;letter-spacing:.3px;display:flex;align-items:center;justify-content:center;gap:8px;border-radius:3px;text-transform:uppercase;box-shadow:0 4px 10px rgba(224,64,27,.25)}
.splash{position:absolute;border-radius:50%;filter:blur(2px)}
.brand{font-weight:800;color:var(--blue);display:flex;align-items:center;gap:10px}
.brand-dot{width:28px;height:28px;border-radius:50%;background:var(--red)}

/* header */
.site-header{top:0;left:0;width:1200px;height:136px;background:var(--white)}
.nav{top:60px;left:346px;display:flex;gap:0;font-size:13px;font-weight:500}
.nav span{margin-right:46px}
.nav .active{color:var(--teal)}
.cart{top:44px;left:1082px;width:52px;height:52px;border-radius:50%;background:var(--red);display:flex;align-items:center;justify-content:center}

/* hero */
.hero{top:136px;left:0;width:1200px;height:536px;background:var(--grey-band)}
.frame{top:198px;left:584px;width:553px;height:411px;background:#e9e9e9;border:14px solid #dcdcdc;box-shadow:0 8px 20px rgba(0,0,0,.18)}
.frame-art{position:absolute;inset:16px;background:linear-gradient(90deg,#6b5a48 0%,#3e3126 45%,#d98a3c 55%,#e8a35a 100%)}
.divider{position:absolute;top:0;bottom:0;width:2px;background:rgba(255,255,255,.8)}
.knob{position:absolute;width:52px;height:52px;border-radius:50%;background:rgba(40,40,40,.55);border:2px solid #fff;display:flex;align-items:center;justify-content:center}

/* slider */
.slide{top:893px;left:292px;width:616px;height:459px;background:linear-gradient(90deg,#5f8f3e 0%,#8fb27a 48%,#c9d8c4 52%,#e9eee9 100%)}
.thumb{position:absolute;top:1367px;width:110px;height:111px}
.arrow-circ{position:absolute;width:66px;height:66px;border-radius:50%;background:var(--red);display:flex;align-items:center;justify-content:center;box-shadow:0 4px 10px rgba(0,0,0,.12)}

/* categories */
.cat-band{top:1670px;left:0;width:1200px;height:1179px;background:var(--sky-band)}
.card{position:absolute;width:446px;height:396px;background:var(--white);box-shadow:0 2px 10px rgba(0,0,0,.04)}
.card-img{position:absolute;top:29px;left:29px;width:388px;height:269px}
.card-label{position:absolute;left:0;width:100%;text-align:center;top:337px;font-size:29px;font-weight:800;color:var(--teal)}

/* steps */
.step-circle{position:absolute;width:126px;height:126px;border-radius:50%;background:var(--red);display:flex;align-items:center;justify-content:center;box-shadow:0 6px 14px rgba(224,64,27,.25)}
.badge{position:absolute;top:-6px;right:-6px;width:28px;height:28px;border-radius:50%;background:var(--teal);color:#fff;font-size:13px;font-weight:700;display:flex;align-items:center;justify-content:center;border:3px solid #fff}
.step-text{position:absolute;font-size:14px;line-height:21px;text-align:center;color:var(--ink)}

/* about */
.about-band{top:3423px;left:0;width:1200px;height:730px;background:var(--grey-band)}
.about-copy{top:3608px;left:215px;width:770px;font-size:13.5px;line-height:21.5px;text-align:center}
.about-copy p{margin-bottom:21px}

/* why */
.why-title{position:absolute;font-size:19px;font-weight:700;color:var(--teal);text-align:center}
.why-text{position:absolute;font-size:13.5px;line-height:20.5px;text-align:center}

/* cta + footer */
.cta{top:4685px;left:0;width:1200px;height:691px;background:linear-gradient(180deg,#2e3a36 0%,#1f2a28 40%,#172020 100%)}
.cta-line1{top:4822px;font-size:40px;font-weight:800;color:#fff}
.cta-line2{top:4870px;font-size:40px;font-weight:900;color:var(--teal)}
.foot-head{position:absolute;font-size:17px;font-weight:700;color:var(--teal)}
.foot-rule{position:absolute;height:1px;background:rgba(255,255,255,.25)}
.foot-link{position:absolute;font-size:13px;color:#e8e8e8}
.social{position:absolute;top:5276px;width:37px;height:37px;border-radius:4px}
</style>
</head>
<body>

<!-- header -->
<header class="abs site-header">
  <div class="abs brand" style="top:52px;left:62px;font-size:24px"><span class="brand-dot"></span>Brushtide Studio</div>
  <nav class="abs nav">
    <span class="active">Home</span><span>Shop</span><span>Testimonials</span><span>About Us</span><span>FAQs</span><span>My Orders</span><span>Contact Us</span>
  </nav>
  <div class="abs cart">
    <svg width="24" height="24" viewBox="0 0 24 24" fill="none" stroke="#fff" stroke-width="2" stroke-linecap="round" stroke-linejoin="round"><path d="M2 3h3l2.5 12h11l2-8H6.5"/><circle cx="9" cy="20" r="1.4"/><circle cx="17" cy="20" r="1.4"/></svg>
  </div>
</header>

<!-- hero -->
<section class="abs hero">
  <div class="abs script" style="top:142px;left:63px;font-size:29px">Turn your Digital Photos Into</div>
  <h1 class="abs heading" style="top:180px;left:63px;font-size:52px;line-height:56px">One of a Kind<br>Wall Art</h1>
  <div class="btn" style="top:331px;left:65px;width:273px;height:57px">Upload a Photo
    <svg width="20" height="20" viewBox="0 0 24 24" fill="none" stroke="#fff" stroke-width="2" stroke-linecap="round"><path d="M12 16V4M7 9l5-5 5 5M4 15v5h16v-5"/></svg>
  </div>
  <div class="splash" role="img" aria-label="Paint splash decoration" style="top:90px;left:1132px;width:80px;height:290px;border-radius:40%;background:radial-gradient(circle,#f2a81c 0%,#e0401b 45%,#2aa3d3 75%,transparent 78%)"></div>
</section>
<div class="abs frame">
  <div class="frame-art" role="img" aria-label="Before and after photo of a dog and an orange cat resting together">
    <div class="divider" style="left:237px"></div>
    <div class="knob" style="left:212px;top:164px"><svg width="22" height="12" viewBox="0 0 22 12" fill="#fff"><path d="M0 6l7-5v10zM22 6l-7-5v10z"/></svg></div>
  </div>
</div>

<!-- from photo to -->
<div class="abs script center" style="top:750px;font-size:35px">From Photo to</div>
<h2 class="abs heading center" style="top:796px;font-size:45px">Museum Quality Canvas Art</h2>
<div class="abs slide" role="img" aria-label="Before and after of a grandfather carrying his grandson on his back outdoors">
  <div class="divider" style="left:306px"></div>
  <div class="knob" style="left:274px;top:200px;width:70px;height:70px"><svg width="26" height="14" viewBox="0 0 22 12" fill="#fff"><path d="M0 6l7-5v10zM22 6l-7-5v10z"/></svg></div>
</div>
<div class="thumb" role="img" aria-label="Horse and rider thumbnail" style="left:292px;background:linear-gradient(135deg,#6f5535,#c9b48e)"></div>
<div class="thumb" role="img" aria-label="Couple portrait thumbnail" style="left:418px;background:linear-gradient(135deg,#5a6b3b,#a88a63)"></div>
<div class="thumb" role="img" aria-label="Selected family photo thumbnail" style="left:543px;background:linear-gradient(135deg,#3fa8cf,#7cc3de)"></div>
<div class="thumb" role="img" aria-label="Family walking thumbnail" style="left:670px;background:linear-gradient(135deg,#7a8c6a,#c5c7b5)"></div>
<div class="thumb" role="img" aria-label="Mother and baby thumbnail" style="left:798px;background:linear-gradient(135deg,#e9d6cc,#f6efe9)"></div>
<div class="arrow-circ" style="top:1088px;left:123px"><svg width="26" height="18" viewBox="0 0 26 18" fill="none" stroke="#fff" stroke-width="2.2" stroke-linecap="round"><path d="M25 9H2M9 2L2 9l7 7"/></svg></div>
<div class="arrow-circ" style="top:1088px;left:1008px"><svg width="26" height="18" viewBox="0 0 26 18" fill="none" stroke="#fff" stroke-width="2.2" stroke-linecap="round"><path d="M1 9h23M17 2l7 7-7 7"/></svg></div>
<div class="btn" style="top:1528px;left:463px;width:274px;height:58px">Get Started
  <svg width="18" height="12" viewBox="0 0 18 12" fill="none" stroke="#fff" stroke-width="1.8"><path d="M0 6h16M11 1l5 5-5 5"/></svg>
</div>
<div class="splash" role="img" aria-label="Paint splash decoration" style="top:1250px;left:-40px;width:140px;height:250px;background:radial-gradient(circle,#f2a81c 0%,#e0401b 35%,#2aa3d3 62%,transparent 66%)"></div>

<!-- categories -->
<section class="abs cat-band">
  <div class="splash" role="img" aria-label="Paint splash decoration" style="top:120px;left:1090px;width:150px;height:240px;background:radial-gradient(circle,#f2a81c 0%,#e0401b 35%,#2aa3d3 62%,transparent 66%)"></div>
  <div class="splash" role="img" aria-label="Paint splash decoration" style="top:540px;left:-50px;width:140px;height:250px;background:radial-gradient(circle,#f2a81c 0%,#e0401b 35%,#2aa3d3 62%,transparent 66%)"></div>
</section>
<h2 class="abs heading center" style="top:1778px;font-size:44px">Categories</h2>
<div class="card" style="top:1872px;left:125px">
  <div class="card-img" role="img" aria-label="Oil painting style wedding couple among flowers" style="background:linear-gradient(135deg,#3d5a22,#8a3a22 60%,#4d6b2b)"></div>
  <div class="card-label">Oil Painting →</div>
</div>
<div class="card" style="top:1872px;left:628px">
  <div class="card-img" role="img" aria-label="Watercolor style mother and baby" style="background:linear-gradient(135deg,#f3e3da,#fbf6f2)"></div>
  <div class="card-label" style="top:331px">Watercolor →</div>
</div>
<div class="card" style="top:2329px;left:125px">
  <div class="card-img" role="img" aria-label="Impressionist style traveller at a canal with gondolas" style="background:linear-gradient(180deg,#6fa8d6,#d8574a 45%,#1fa89a 70%,#2a7fb0)"></div>
  <div class="card-label">Impressionism →</div>
</div>
<div class="card" style="top:2329px;left:628px">
  <div class="card-img" role="img" aria-label="Digital photo of two children eating ice cream" style="background:linear-gradient(135deg,#7d9b5e,#e7d4bf 55%,#9ac1d0)"></div>
  <div class="card-label">Digital Photo →</div>
</div>

<!-- how it works -->
<h2 class="abs heading center" style="top:2973px;font-size:44px">How it Works</h2>
<svg class="abs" style="top:3090px;left:180px" width="860" height="70" fill="none" stroke="#7fc3e0" stroke-width="2" stroke-dasharray="6 6"><path d="M8 45 Q 80 60 150 40"/><path d="M268 28 Q 360 0 440 30"/><path d="M565 45 Q 660 70 760 40"/></svg>
<div class="step-circle" style="top:3067px;left:62px"><div class="badge">1</div>
  <svg width="54" height="54" viewBox="0 0 24 24" fill="none" stroke="#fff" stroke-width="1.3" stroke-linecap="round"><path d="M12 3a9 9 0 1 0 0 18c1.5 0 1.8-1.2 1.2-2-.7-1 0-2.2 1.2-2.2H17a4 4 0 0 0 4-4C21 7 17 3 12 3z"/><circle cx="7.5" cy="11" r="1.2"/><circle cx="10" cy="7" r="1.2"/><circle cx="15" cy="7.5" r="1.2"/></svg></div>
<div class="step-circle" style="top:3067px;left:323px"><div class="badge">2</div>
  <svg width="54" height="54" viewBox="0 0 24 24" fill="none" stroke="#fff" stroke-width="1.3" stroke-linecap="round" stroke-linejoin="round"><path d="M14 5H5a2 2 0 0 0-2 2v11a2 2 0 0 0 2 2h13a2 2 0 0 0 2-2v-6"/><path d="M3 16l5-5 4 4 3-3 5 5"/><circle cx="8" cy="9" r="1.3"/><path d="M19 9V2M16 5l3-3 3 3"/></svg></div>
<div class="step-circle" style="top:3067px;left:619px"><div class="badge">3</div>
  <svg width="54" height="54" viewBox="0 0 24 24" fill="none" stroke="#fff" stroke-width="1.3" stroke-linejoin="round"><path d="M21 3L3 10l7 3 3 7z"/><path d="M10 13l11-10"/></svg></div>
<div class="step-circle" style="top:3067px;left:947px"><div class="badge">4</div>
  <svg width="58" height="58" viewBox="0 0 24 24" fill="none" stroke="#fff" stroke-width="1.3" stroke-linejoin="round"><path d="M3 8l9-4 9 4-9 4z"/><path d="M3 8v8l9 4 9-4V8"/><path d="M12 12v8"/><path d="M7.5 6l9 4"/></svg></div>
<div class="step-text" style="top:3214px;left:55px;width:140px">Choose your<br>Art Style</div>
<div class="step-text" style="top:3214px;left:276px;width:220px">Upload your photo and<br>choose your canvas size and<br>orientation.</div>
<div class="step-text" style="top:3214px;left:572px;width:220px">Submit your order and<br>check out using our secure<br>and encrypted checkout<br>page</div>
<div class="step-text" style="top:3214px;left:870px;width:280px">We will send your finished design to<br>the email address you provide within<br>48 hours to approve. Once approved,<br>your artwork will be printed,<br>packaged and shipped</div>

<!-- about -->
<section class="abs about-band">
  <div class="splash" role="img" aria-label="Paint splash decoration" style="top:-20px;left:1080px;width:160px;height:250px;background:radial-gradient(circle,#f2a81c 0%,#e0401b 35%,#2aa3d3 62%,transparent 66%)"></div>
  <div class="splash" role="img" aria-label="Paint splash decoration" style="top:250px;left:-50px;width:160px;height:280px;background:radial-gradient(circle,#f2a81c 0%,#e0401b 35%,#2aa3d3 62%,transparent 66%)"></div>
</section>
<h2 class="abs heading center" style="top:3540px;font-size:44px">About Us</h2>
<div class="abs about-copy">
  <p>At Brushtide Studio, we take your digital photo and turn it into a one-of-a-kind piece of artwork!</p>
  <p>The process couldn't be any easier. Simply upload your photo, choose your art style and size, and let our team of skilled digital artists do the rest. Do you want to put your digital photo on canvas without an art style? No problem! Just choose the "Digital Photo/Retouching" category and upload your photo. We can print your photo "as is" or do some minor retouching (e.g. remove objects, enhance colors, lighten photo, etc)</p>
  <p>You will receive a proof in your email to approve within 1-2 days. Once approved, your customized artwork will be transferred to canvas and shipped from our design studio in Florida.</p>
  <p>Brushtide Studio art makes a great gift for just about any special occasion. Know someone with an upcoming birthday, anniversary, housewarming party, wedding or other event? We've got you covered!</p>
  <p>Turn your cherished memories into a customized canvas masterpiece today!</p>
</div>
<div class="btn" style="top:3951px;left:463px;width:274px;height:57px">Get Started
  <svg width="18" height="12" viewBox="0 0 18 12" fill="none" stroke="#fff" stroke-width="1.8"><path d="M0 6h16M11 1l5 5-5 5"/></svg>
</div>

<!-- why choose us -->
<h2 class="abs heading center" style="top:4218px;font-size:44px">Why Choose Us</h2>
<div class="step-circle" style="top:4305px;left:192px">
  <svg width="54" height="54" viewBox="0 0 24 24" fill="none" stroke="#fff" stroke-width="1.3" stroke-linecap="round"><path d="M9 18h6M10 21h4M12 3a6 6 0 0 0-3.5 10.9c.6.5 1 1.2 1 2V16h5v-.1c0-.8.4-1.5 1-2A6 6 0 0 0 12 3z"/><path d="M12 0.5v1M4 4l.8.8M20 4l-.8.8"/></svg></div>
<div class="step-circle" style="top:4305px;left:536px">
  <svg width="60" height="60" viewBox="0 0 24 24" fill="none" stroke="#fff" stroke-width="1.3" stroke-linejoin="round"><path d="M2 6h13v10H2zM15 9h4l3 4v3h-7z"/><circle cx="6" cy="17.5" r="1.6"/><circle cx="18" cy="17.5" r="1.6"/><path d="M5 9h6M5 12h4"/></svg></div>
<div class="step-circle" style="top:4305px;left:884px">
  <svg width="54" height="54" viewBox="0 0 24 24" fill="none" stroke="#fff" stroke-width="1.3" stroke-linejoin="round"><circle cx="12" cy="9" r="6.5"/><path d="M12 5.5l1 2.2 2.4.3-1.8 1.6.5 2.4-2.1-1.2-2.1 1.2.5-2.4L8.6 8l2.4-.3z"/><path d="M8 14.5L6 22l3-1.5 2 2 1-6M16 14.5l2 7.5-3-1.5-2 2-1-6"/></svg></div>
<div class="why-title" style="top:4455px;left:105px;width:300px">Your Idea Your Design</div>
<div class="why-title" style="top:4455px;left:449px;width:300px">Fast Shipping</div>
<div class="why-title" style="top:4455px;left:797px;width:300px">High Quality</div>
<div class="why-text" style="top:4494px;left:105px;width:300px">Each art piece is customized for you!<br>You choose your size, orientation and<br>art style. Makes a perfect gift!!!</div>
<div class="why-text" style="top:4494px;left:449px;width:300px">Your artwork is printed and shipped<br>in the USA! We offer fast turnaround<br>with transit times typically 3-7 days.<br>Free tracking with each order!!</div>
<div class="why-text" style="top:4494px;left:797px;width:300px">We've put a lot of effort ensuring<br>your artwork is of the highest quality.<br>Each piece is printed on the highest<br>quality, gallery grade canvas. It is<br>ready to hang upon arrival.!</div>

<!-- call to action + footer -->
<section class="abs cta" role="img" aria-label="Dim background photo of a parent and child walking outdoors"></section>
<div class="abs center cta-line1">Let’s Create a</div>
<div class="abs center cta-line2">Masterpiece Today!</div>
<div class="btn" style="top:4946px;left:463px;width:274px;height:57px">Get Started
  <svg width="18" height="12" viewBox="0 0 18 12" fill="none" stroke="#fff" stroke-width="1.8"><path d="M0 6h16M11 1l5 5-5 5"/></svg>
</div>

<div class="abs brand" style="top:5128px;left:125px;font-size:22px;color:#fff"><span class="brand-dot"></span>Brushtide Studio</div>

<div class="foot-head" style="top:5102px;left:434px">Navigation</div>
<div class="foot-rule" style="top:5136px;left:434px;width:298px"></div>
<div class="foot-link" style="top:5158px;left:434px">About Us</div>
<div class="foot-link" style="top:5192px;left:434px">Testimonials</div>
<div class="foot-link" style="top:5223px;left:434px">FAQs</div>
<div class="foot-link" style="top:5158px;left:580px">My Orders</div>
<div class="foot-link" style="top:5192px;left:580px">Privacy Policy</div>
<div class="foot-link" style="top:5223px;left:580px">Terms and Conditions</div>

<div class="foot-head" style="top:5102px;left:870px">Contact</div>
<div class="foot-rule" style="top:5136px;left:870px;width:230px"></div>
<div class="foot-link" style="top:5158px;left:870px">hello@brushtidestudio.com</div>
<div class="foot-link" style="top:5192px;left:870px;line-height:18px">Brushtide Studio<br>2870 Harbor Mill Rd #208 Port Lenora,<br>Florida 34190</div>
<div class="social" style="left:870px;background:#3b5ea8"></div>
<div class="social" style="left:913px;background:#c23a8a"></div>
<div class="social" style="left:956px;background:#c8202c"></div>
<div class="social" style="left:999px;background:#2aa3d3"></div>

</body>
</html>
```